We are looking to create a graphic that will be used in Facebook posts each week to show the daily Mosquito Forecast. Attached is an example of what we are looking for. We need to be able to update the forecast. So we will need hi-res vector files. The graphics need to represent the level of mosquito activity: SLIGHT, AVERAGE, INTENSE, EXTREME

```html
<!DOCTYPE html>
<html lang="en">
<head>
<meta charset="utf-8">
<title>Mosquito Forecast</title>
<link rel="stylesheet" href="https://fonts.googleapis.com/css2?family=Open+Sans:wght@400;600;700&family=Poppins:wght@500;600;700&display=swap">
<style>
  :root{
    --band-a:#a2df5c;
    --band-b:#12e3aa;
    --white:#ffffff;
    --ink:#1c1c1c;
    --muted:#555b60;
    --ring:#d4d8dd;
    --knob:#3b3b3b;
    --slight:#0e8d3a;
    --average:#f1b500;
    --intense:#ff4e14;
    --extreme:#b10f10;
    --gold:#f7b500;
    --divider:#c9cdd1;
  }
  *{box-sizing:border-box;margin:0;padding:0}
  html,body{width:1200px;height:1014px;overflow:hidden;background:var(--white)}
  body{position:relative;font-family:"Open Sans",Arial,sans-serif;color:var(--ink)}
  .defs{position:absolute;width:0;height:0}

  .hero-band{position:absolute;left:0;top:0;width:1200px;height:792px;
    background:linear-gradient(to top right,var(--band-a) 0%,#52e08a 45%,var(--band-b) 100%)}
  .board-title{position:absolute;top:46px;width:100%;text-align:center;color:var(--white);
    font-weight:700;font-size:58px;line-height:1;letter-spacing:.3px}
  .board-sub{position:absolute;top:134px;width:100%;text-align:center;color:var(--white);
    font-weight:600;font-size:24px}

  .post{position:absolute;left:52px;top:188px;width:1062px;height:558px;overflow:hidden}
  .post-photo{position:absolute;inset:0;
    background:
      linear-gradient(180deg,rgba(168,205,235,.0) 0%,rgba(0,0,0,0) 100%),
      linear-gradient(180deg,#6f8e4a 0%,#3f6a2a 30%,#2f4f22 55%,#405a3c 75%,#6a7f7a 100%)}
  .post-photo::before{content:"";position:absolute;left:420px;top:0;width:300px;height:120px;
    background:radial-gradient(ellipse at center,rgba(220,232,245,.85) 0%,rgba(150,190,225,.5) 45%,rgba(0,0,0,0) 75%)}
  .post-title{position:absolute;top:80px;width:100%;text-align:center;color:var(--white);
    font-family:"Poppins",Arial,sans-serif;font-weight:600;font-size:82px;line-height:1;letter-spacing:-1px;
    text-shadow:0 3px 8px rgba(0,0,0,.35)}
  .post-region{position:absolute;top:160px;width:100%;text-align:center;color:var(--gold);
    font-family:"Poppins",Arial,sans-serif;font-weight:500;font-size:43px;line-height:1;
    text-shadow:0 2px 6px rgba(0,0,0,.4)}

  .forecast{position:absolute;left:18px;top:234px;width:1026px;height:280px;background:var(--white);
    display:flex;font-family:"Poppins",Arial,sans-serif}
  .day{position:relative;flex:1;text-align:center}
  .day + .day::before{content:"";position:absolute;left:0;top:16px;height:184px;width:1px;background:var(--divider)}
  .day-name{margin-top:38px;font-size:13px;font-weight:600;color:var(--ink)}
  .day-date{margin-top:4px;font-size:10px;color:var(--muted)}
  .gauge{display:block;margin:12px auto 0;width:130px;height:130px}
  .level{margin-top:8px;font-size:16px;font-weight:600}
  .is-slight{color:var(--slight)} .is-average{color:var(--average)}
  .is-intense{color:var(--intense)} .is-extreme{color:var(--extreme)}

  .legend{position:absolute;left:0;top:792px;width:1200px;height:222px;background:var(--white)}
  .legend-gauge{position:absolute;left:188px;top:40px;width:144px;height:144px}
  .legend-text{position:absolute;left:367px;top:68px;font-size:19px;color:#333}
  .legend-key{font-size:21px;font-weight:600;margin-bottom:8px}
  .legend-key .sep{color:#333;margin:0 8px;font-weight:400}
  .legend-text p{line-height:29px}
</style>
</head>
<body>

<svg class="defs" aria-hidden="true">
  <defs>
    <linearGradient id="levelScale" x1="0" y1="0" x2="1" y2="0">
      <stop offset="0" stop-color="#1a9b3c"/>
      <stop offset=".28" stop-color="#d8c414"/>
      <stop offset=".45" stop-color="#f57a14"/>
      <stop offset=".7" stop-color="#d8211a"/>
      <stop offset="1" stop-color="#a50d10"/>
    </linearGradient>
    <filter id="soft" x="-20%" y="-20%" width="140%" height="140%">
      <feDropShadow dx="0" dy="1" stdDeviation="2" flood-opacity=".25"/>
    </filter>
    <symbol id="dial" viewBox="0 0 130 130">
      <circle cx="65" cy="65" r="54" fill="none" stroke="var(--ring)" stroke-width="10"/>
      <path d="M26.82 103.18 A54 54 0 1 1 103.18 103.18" fill="none" stroke="url(#levelScale)" stroke-width="9" stroke-linecap="round"/>
      <circle cx="65" cy="65" r="46" fill="#fff" filter="url(#soft)"/>
    </symbol>
  </defs>
</svg>

<header class="hero-band">
  <h1 class="board-title">Mosquito Forecast</h1>
  <p class="board-sub">Mockup 2- size 1200X630 px | Vector Format</p>

  <section class="post">
    <div class="post-photo" role="img" aria-label="Summer photo of a wooden covered bridge over a calm pond surrounded by green trees"></div>
    <h2 class="post-title">Moscuito Forecast</h2>
    <p class="post-region">Greater Milwakukee</p>

    <div class="forecast">
      <div class="day">
        <div class="day-name">Mon Day</div><div class="day-date">02/20</div>
        <svg class="gauge" viewBox="0 0 130 130"><use href="#dial"/>
          <g role="img" aria-label="Green mosquito silhouette"><circle cx="65" cy="65" r="27" fill="var(--slight)"/></g>
          <circle cx="14.2" cy="46.5" r="9" fill="var(--knob)" stroke="#fff" stroke-width="3"/></svg>
        <div class="level is-slight">Slight</div>
      </div>
      <div class="day">
        <div class="day-name">Tues Day</div><div class="day-date">02/21</div>
        <svg class="gauge" viewBox="0 0 130 130"><use href="#dial"/>
          <g role="img" aria-label="Yellow mosquito silhouette"><circle cx="65" cy="65" r="27" fill="var(--average)"/></g>
          <circle cx="60.3" cy="11.2" r="9" fill="var(--knob)" stroke="#fff" stroke-width="3"/></svg>
        <div class="level is-average">Average</div>
      </div>
      <div class="day">
        <div class="day-name">Wednes Day</div><div class="day-date">02/22</div>
        <svg class="gauge" viewBox="0 0 130 130"><use href="#dial"/>
          <g role="img" aria-label="Orange mosquito silhouette"><circle cx="65" cy="65" r="27" fill="var(--intense)"/></g>
          <circle cx="111.8" cy="38" r="9" fill="var(--knob)" stroke="#fff" stroke-width="3"/></svg>
        <div class="level is-intense">Intense</div>
      </div>
      <div class="day">
        <div class="day-name">Thurs Day</div><div class="day-date">02/23</div>
        <svg class="gauge" viewBox="0 0 130 130"><use href="#dial"/>
          <g role="img" aria-label="Red mosquito silhouette"><circle cx="65" cy="65" r="27" fill="var(--extreme)"/></g>
          <circle cx="111.8" cy="92" r="9" fill="var(--knob)" stroke="#fff" stroke-width="3"/></svg>
        <div class="level is-extreme">Extreme</div>
      </div>
      <div class="day">
        <div class="day-name">Fri Day Day</div><div class="day-date">02/24</div>
        <svg class="gauge" viewBox="0 0 130 130"><use href="#dial"/>
          <g role="img" aria-label="Green mosquito silhouette"><circle cx="65" cy="65" r="27" fill="var(--slight)"/></g>
          <circle cx="14.2" cy="46.5" r="9" fill="var(--knob)" stroke="#fff" stroke-width="3"/></svg>
        <div class="level is-slight">Slight</div>
      </div>
      <div class="day">
        <div class="day-name">Satur Day</div><div class="day-date">02/25</div>
        <svg class="gauge" viewBox="0 0 130 130"><use href="#dial"/>
          <g role="img" aria-label="Yellow mosquito silhouette"><circle cx="65" cy="65" r="27" fill="var(--average)"/></g>
          <circle cx="60.3" cy="11.2" r="9" fill="var(--knob)" stroke="#fff" stroke-width="3"/></svg>
        <div class="level is-average">Average</div>
      </div>
      <div class="day">
        <div class="day-name">Sun Day</div><div class="day-date">02/26</div>
        <svg class="gauge" viewBox="0 0 130 130"><use href="#dial"/>
          <g role="img" aria-label="Red mosquito silhouette"><circle cx="65" cy="65" r="27" fill="var(--extreme)"/></g>
          <circle cx="111.8" cy="92" r="9" fill="var(--knob)" stroke="#fff" stroke-width="3"/></svg>
        <div class="level is-extreme">Extreme</div>
      </div>
    </div>
  </section>
</header>

<section class="legend">
  <svg class="legend-gauge" viewBox="0 0 130 130"><use href="#dial"/>
    <g role="img" aria-label="Red mosquito silhouette"><circle cx="65" cy="65" r="27" fill="var(--extreme)"/></g>
    <circle cx="111.8" cy="92" r="8" fill="var(--knob)" stroke="#fff" stroke-width="3"/></svg>
  <div class="legend-text">
    <div class="legend-key">
      <span class="is-slight">Slight: Green</span><span class="sep">|</span><span class="is-average">Average: Yellow</span><span class="sep">|</span><span class="is-intense">Intense : Orange</span><span class="sep">|</span><span class="is-extreme">Intense: RED</span>
    </div>
    <p>Slide stopper is used in this slider</p>
    <p>Mosquite color also changed as per the forecast</p>
  </div>
</section>

</body>
</html>
```